Business Card Design - Property Management & Real Estate Services

I need a business card design for my company that I can print ZEPLA Cards. The company is called Brindle Management Company. It is a property management and real estate company. The design has to be clean and modern. I need two versions. One for my employee and one for me. However, the design will be the same, just different text. You can get a feel for the company by looking at our website at www.brindlemanagement.example.

Industry/Entity Type

Property Management

Contact Information for Business Card

I will be using ZEPLA.com to print my cards. I will most likely use the rounded edges card. I need two versions, however, they will be the same design. I need one for me and my employee.

Colors
3276b5
33a6d7

Requirements
Must have
• Company Logo
• Name of person
• Property Management & Real Estate Service
• Phone
• Email
• Website
• Address
• A space to place a QR code

```html
<!DOCTYPE html>
<html lang="en">
<head>
<meta charset="utf-8">
<title>Brindle Management – Business Cards</title>
<link href="https://fonts.googleapis.com/css2?family=Roboto:wght@400;500&family=Roboto+Condensed:wght@700&display=swap" rel="stylesheet">
<style>
  :root {
    --backdrop: #d3d3d3;
    --card: #ffffff;
    --brand-blue: #1f56b0;
    --brand-light: #5e97d6;
    --text-dark: #3a3a3a;
    --qr-line: #b9c6d8;
  }
  * { box-sizing: border-box; margin: 0; padding: 0; }
  html, body { width: 1200px; height: 852px; overflow: hidden; }
  body {
    background: var(--backdrop);
    font-family: "Roboto", Arial, sans-serif;
    position: relative;
  }
  .card {
    position: absolute;
    top: 276px;
    width: 520px;
    height: 300px;
    background: var(--card);
    border-radius: 18px;
    overflow: hidden;
    box-shadow: 0 6px 18px rgba(0,0,0,0.18);
  }
  .card--front { left: 50px; }
  .card--back { left: 630px; }

  .brand-name {
    display: flex;
    align-items: center;
    gap: 10px;
    font-family: "Roboto", Arial, sans-serif;
    font-weight: 500;
    color: var(--brand-blue);
    white-space: nowrap;
  }
  .brand-name__mark {
    flex: none;
    background: var(--brand-blue);
  }
  .card--front .brand-name {
    position: absolute;
    top: 88px; left: 0; right: 0;
    justify-content: center;
    font-size: 34px;
  }
  .card--front .brand-name__mark { width: 22px; height: 22px; }
  .tagline {
    position: absolute;
    top: 138px; left: 0; right: 0;
    text-align: center;
    font-size: 14px;
    color: var(--text-dark);
  }
  .front-web {
    position: absolute;
    top: 196px; left: 0; right: 0;
    display: flex; align-items: center; justify-content: center; gap: 14px;
    font-size: 15px; color: var(--text-dark);
  }
  .front-web::before, .front-web::after {
    content: ""; width: 40px; height: 2px; background: var(--brand-blue);
  }
  .band { position: absolute; left: 0; bottom: 0; width: 100%; }

  .card--back .brand-name {
    position: absolute;
    top: 60px; left: 30px;
    font-size: 19px;
    gap: 8px;
  }
  .card--back .brand-name__mark { width: 14px; height: 14px; }
  .qr-space {
    position: absolute;
    top: 110px; left: 30px;
    width: 76px; height: 76px;
    border: 1.5px dashed var(--qr-line);
    border-radius: 4px;
  }
  .contact {
    position: absolute;
    top: 52px; left: 262px;
    color: var(--text-dark);
  }
  .contact__name {
    font-family: "Roboto Condensed", Arial, sans-serif;
    font-weight: 700;
    font-size: 20px;
    color: var(--brand-blue);
  }
  .contact__role { font-size: 13px; margin: 2px 0 14px; }
  .contact__list { list-style: none; font-size: 13px; }
  .contact__list li { display: flex; align-items: center; gap: 8px; margin-bottom: 4px; }
  .contact__list svg { width: 12px; height: 12px; fill: var(--text-dark); flex: none; }
  .address-band {
    position: absolute; left: 0; bottom: 0; width: 100%; height: 54px;
    background: var(--brand-blue);
    color: #fff; font-size: 15px;
    display: flex; align-items: center; justify-content: center;
  }
  .address-rule {
    position: absolute; left: 0; bottom: 60px; width: 100%; height: 2px;
    background: var(--brand-blue);
  }
</style>
</head>
<body>
  <section class="card card--front" aria-label="Card front">
    <div class="brand-name"><span class="brand-name__mark"></span>Brindle Management</div>
    <div class="tagline">Property Management &amp; Real Estate Services</div>
    <div class="front-web">www.brindlemanagement.example</div>
    <svg class="band" width="520" height="16" viewBox="0 0 520 16" aria-hidden="true">
      <rect x="0" y="6" width="230" height="10" fill="var(--brand-light)"/>
      <polygon points="220,16 240,0 520,0 520,16" fill="var(--brand-blue)"/>
    </svg>
  </section>

  <section class="card card--back" aria-label="Card back">
    <div class="brand-name"><span class="brand-name__mark"></span>Brindle Management</div>
    <div class="qr-space" role="img" aria-label="Space reserved for a QR code"></div>
    <div class="contact">
      <div class="contact__name">Marisol T. Ocampo</div>
      <div class="contact__role">Founder</div>
      <ul class="contact__list">
        <li><svg viewBox="0 0 12 12"><path d="M2 1h3l1 3-1.5 1a6 6 0 0 0 2.5 2.5L8 6l3 1v3a1 1 0 0 1-1 1A9 9 0 0 1 1 2a1 1 0 0 1 1-1z"/></svg>(305) 555-0147</li>
        <li><svg viewBox="0 0 12 12"><path d="M1 2h10v8H1z M1 2l5 4 5-4" stroke="#fff" stroke-width="0.8"/></svg>marisol@brindlemanagement.example</li>
        <li><svg viewBox="0 0 12 12"><circle cx="6" cy="6" r="5"/><path d="M1 6h10M6 1v10" stroke="#fff" stroke-width="0.8"/></svg>www.brindlemanagement.example</li>
      </ul>
    </div>
    <div class="address-rule"></div>
    <div class="address-band">480 Harbor Lane #210 Bayview, FL 33000</div>
  </section>
</body>
</html>
```